Landing Page for Church Launch

We are a new Christian Church Plant in Milwaukee Wisconsin. I would like an exciting and unique landing page for people who are interested in:
1) What our ministry is about
2) When our ministry will be launching
3) Those who may want to join our launch team
4) Those who may want give financially into our vision
5) Those who want to follow us and get more information about us
I would also love for our color scheme to be reflective of our logo.
I included more detailed instructions and what we are looking for in the enclosed document
Religious/Christian

```html
<!DOCTYPE html>
<html lang="en">
<head>
<meta charset="utf-8">
<title>Renew Church – Launch</title>
<link href="https://fonts.googleapis.com/css2?family=Montserrat:wght@500;600;700&family=Roboto:wght@400;500;700&display=swap" rel="stylesheet">
<style>
:root{
  --navy:#14137a;
  --navy-deep:#0d0c5c;
  --red:#d0151b;
  --red-deep:#b50f14;
  --ink:#222;
  --muted:#707070;
  --light:#f2f2f3;
  --card:#f7eeee;
  --footer:#1b1b1b;
  --white:#fff;
}
*{box-sizing:border-box;margin:0;padding:0}
html,body{width:1200px;height:5259px;overflow:hidden}
body{position:relative;font-family:"Roboto",sans-serif;color:var(--ink);background:var(--white)}
.abs{position:absolute}
.heading{position:absolute;left:0;width:1200px;text-align:center;font-family:"Montserrat",sans-serif;font-weight:600;font-size:29px;letter-spacing:1px;color:#1c1c1c}
.heading::before{content:"";display:inline-block;width:4px;height:40px;background:var(--red);margin-right:14px;vertical-align:-8px}

/* hero */
.hero{position:absolute;left:0;top:0;width:1200px;height:704px;overflow:hidden}
.hero-photo{position:absolute;inset:0;background:linear-gradient(100deg,#3b3f45 0%,#7a6558 35%,#a07e68 50%,#6d5a52 70%,#3e4350 100%)}
.hero-photo::after{content:"";position:absolute;inset:0;background:rgba(20,15,20,.25)}
.brand{position:absolute;left:110px;top:36px;display:flex;align-items:center;gap:8px;font-family:"Montserrat",sans-serif;font-weight:700;font-size:34px;color:var(--white);letter-spacing:1px}
.brand i{width:14px;height:14px;background:var(--red)}
.menu{position:absolute;left:1046px;top:30px;width:40px;height:32px}
.hero-text{position:absolute;left:0;width:1200px;text-align:center;color:var(--white)}
.kicker{font-family:"Montserrat",sans-serif;font-weight:600;font-size:15px;letter-spacing:.5px}
.date{top:298px;font-family:"Montserrat",sans-serif;font-weight:700;font-size:42px;color:var(--red)}
.countdown{position:absolute;left:470px;top:414px;display:flex;gap:22px}
.count{width:50px;text-align:center;color:var(--white)}
.count b{display:block;height:50px;line-height:50px;background:var(--navy);font-family:"Montserrat",sans-serif;font-size:20px;font-weight:600}
.count span{display:block;margin-top:8px;font-size:9px;font-weight:700}

/* vision band */
.vm{position:absolute;left:0;top:812px;width:1200px;height:380px}
.vm h3{font-family:"Montserrat",sans-serif;font-weight:500;font-size:34px;margin-bottom:14px}
.vm p{font-size:18px;line-height:30px;font-weight:500}
.vm-block{position:absolute;text-align:center;color:var(--white)}

/* launch */
.intro{position:absolute;left:250px;top:1310px;width:700px;text-align:center;font-size:13.5px;line-height:26px;color:var(--muted)}
.portrait-back{position:absolute;left:108px;top:1432px;width:472px;height:666px;background:#e3e1ea}
.portrait{position:absolute;left:108px;top:1418px;width:484px;height:664px;background:linear-gradient(160deg,#dfe6ea,#a9b3bd 45%,#5b5d6b 75%,#42404e);box-shadow:0 0 18px rgba(0,0,0,.15);border:6px solid #fff}
.launch-col{position:absolute;left:635px;top:1428px;width:460px;font-size:13.5px;color:var(--muted)}
.ticks li{list-style:none;position:relative;padding-left:26px;margin-bottom:19px}
.ticks li::before{content:"";position:absolute;left:0;top:2px;width:13px;height:13px;border-radius:50%;background:var(--red)}
.ticks li::after{content:"";position:absolute;left:4px;top:5px;width:4px;height:6px;border:solid #fff;border-width:0 2px 2px 0;transform:rotate(45deg)}
.launch-col p{line-height:26px}
.launch-col h4{color:var(--ink);font-size:14px;font-weight:500;margin:32px 0 12px}
.btn{display:inline-block;width:200px;height:46px;line-height:46px;text-align:center;color:#fff;font-size:12px;font-weight:700;margin-top:18px}
.btn.red{background:var(--red)}
.btn.navy{background:var(--navy)}

/* core values */
.values{position:absolute;left:0;top:2193px;width:1200px;height:983px;background:linear-gradient(#efeff0,#f3f3f4 60%,#e9e9eb)}
.vcard{position:absolute;width:184px;height:143px;background:var(--card);box-shadow:0 4px 14px rgba(0,0,0,.05)}
.vcard div{position:absolute;left:52px;top:32px;width:80px;height:80px;border-radius:8px;background:linear-gradient(#e4dede,#d5cdcd)}
.vlabel{position:absolute;width:260px;text-align:center;font-size:15px;color:#333}
.ring{position:absolute;left:412px;top:2536px;width:388px;height:388px;border-radius:50%;background:var(--navy)}
.ring-inner{position:absolute;left:62px;top:62px;width:264px;height:264px;border-radius:50%;background:#fff;display:flex;align-items:center;justify-content:center;font-family:"Montserrat",sans-serif;font-weight:700;font-size:50px;color:var(--navy);gap:10px}
.ring-inner i{width:16px;height:16px;background:var(--navy)}

/* why */
.why{position:absolute;left:112px;top:3356px;width:486px;font-size:14px;line-height:25px;color:#555}
.why li{list-style:none;position:relative;padding-left:28px;margin-bottom:15px}
.why li::before{content:"";position:absolute;left:0;top:6px;width:12px;height:12px;border-radius:50%;border:2px solid var(--red)}
.why li::after{content:"";position:absolute;left:4px;top:10px;width:4px;height:4px;border-radius:50%;background:var(--red)}
.video-back{position:absolute;left:694px;top:3338px;width:394px;height:388px;background:#fbe6e6}
.video{position:absolute;left:673px;top:3352px;width:396px;height:402px;background:linear-gradient(#9a87c0,#c994b6 40%,#d08a7d 65%,#4a2f3c)}
.video-frame{position:absolute;left:657px;top:3385px;width:386px;height:386px;border:2px solid var(--red-deep)}

/* community */
.community{position:absolute;left:0;top:3862px;width:1200px;height:692px;background:linear-gradient(90deg,#2a0d7a,#5a0f5e 50%,#b5121b)}
.community p{position:absolute;left:170px;top:141px;width:860px;text-align:center;color:#fff;font-size:14.5px;line-height:26px}
.group-photo{position:absolute;left:280px;top:242px;width:640px;height:380px;background:linear-gradient(120deg,#8c6a55,#c8a07f 40%,#6f7aa0 70%,#4a4d6a)}

/* pastor */
.pastor-photo{position:absolute;left:112px;top:4641px;width:245px;height:378px;background:linear-gradient(#6d6e7a,#3f4150);border-radius:120px 120px 0 0}
.pastor-list{position:absolute;left:376px;top:4780px;width:340px;font-size:14.5px;color:var(--muted);line-height:22px}
.pastor-list li{list-style:none;position:relative;padding-left:30px;margin-bottom:20px}
.pastor-list li::before{content:"»";position:absolute;left:0;top:-4px;font-size:24px;color:#222;font-weight:700}
.form{position:absolute;left:749px;top:4753px;width:340px;height:395px;background:#fff;box-shadow:0 6px 24px rgba(0,0,0,.15)}
.form h3{height:64px;line-height:64px;background:var(--navy);color:#fff;text-align:center;font-family:"Montserrat",sans-serif;font-weight:600;font-size:23px}
.field{margin:26px 40px 0;height:28px;border-bottom:1px solid #ddd;font-size:11px;color:#555}
.submit{margin:30px 40px 0;height:44px;line-height:44px;background:var(--red);color:#fff;text-align:center;font-weight:700;font-size:13px}

/* footer */
.footer{position:absolute;left:0;top:5019px;width:1200px;height:240px;background:var(--footer);color:#fff}
.contact{position:absolute;display:flex;gap:16px;align-items:flex-start}
.contact .ic{width:40px;height:40px;border-radius:50%;background:#fff;display:flex;align-items:center;justify-content:center}
.contact b{display:block;font-size:16px;font-weight:700;margin-bottom:4px}
.contact span{font-size:14px;line-height:19px;color:#ddd}
.copy{position:absolute;left:110px;top:211px;font-size:12px;color:#ddd}
.social{position:absolute;left:998px;top:202px;display:flex;gap:8px}
.social i{width:24px;height:24px;border-radius:50%;background:var(--red)}
</style>
</head>
<body>

<section class="hero">
  <div class="hero-photo" role="img" aria-label="Smiling woman greeting people in a welcoming crowd"></div>
  <div class="brand"><i></i>RENEW</div>
  <svg class="menu" viewBox="0 0 40 32"><rect y="3" width="40" height="3" fill="#fff"/><rect y="14" width="40" height="3" fill="#fff"/><rect y="25" width="40" height="3" fill="#fff"/></svg>
  <div class="hero-text kicker" style="top:274px">WE ARE COMING</div>
  <div class="hero-text date">September 10, 2023 AT 5PM</div>
  <div class="hero-text kicker" style="top:376px;font-size:14px">REVIVAL IS COMING</div>
  <div class="countdown">
    <div class="count"><b>221</b><span>DAYS</span></div>
    <div class="count"><b>06</b><span>HOURS</span></div>
    <div class="count"><b>56</b><span>MINS</span></div>
    <div class="count"><b>33</b><span>SEC</span></div>
  </div>
  <svg class="abs" style="left:0;top:560px" width="1200" height="144" viewBox="0 0 1200 144">
    <polygon points="0,144 0,140 560,40 600,50 1200,112 1200,144" fill="#fff"/>
    <polygon points="600,50 1200,14 1200,112" fill="#d0151b"/>
    <polygon points="600,50 1200,60 1200,112" fill="#14137a"/>
  </svg>
</section>

<h2 class="heading" style="top:752px">MISSION AND VISION</h2>

<section class="vm">
  <svg class="abs" style="left:0;top:0" width="1200" height="380" viewBox="0 0 1200 380">
    <polygon points="0,0 600,74 600,318 0,380" fill="#14137a"/>
    <polygon points="600,74 1200,0 1200,380 600,318" fill="#d0151b"/>
  </svg>
  <div class="vm-block" style="left:50px;top:126px;width:500px"><h3>Vision</h3><p>A Faith Community established to connect YOU to Jesus, YOUR Purpose, and the Community YOU serve.</p></div>
  <div class="vm-block" style="left:650px;top:98px;width:500px"><h3>Mission</h3><p>To be the spiritual destination of choice for those seeking to connect to Jesus in a Christ-Centered, Multi-Ethnic community that serves families with and without special needs.</p></div>
</section>

<h2 class="heading" style="top:1248px">LAUNCH TEAM</h2>
<p class="intro">Renew is tentatively scheduled to reopen physical doors on September 16, 2023. In preparation for those we are called to serve, we will have a launch team to help lay the groundwork to make a lasting impact and change in our community. Some of the asks of the launch team will be:</p>
<div class="portrait-back"></div>
<div class="portrait" role="img" aria-label="Portrait of the pastor in a checked blazer"></div>
<div class="launch-col">
  <ul class="ticks">
    <li>Pray for the church</li>
    <li>Attend monthly launch team meetings (For Planning and Strategy)</li>
    <li>Invite others to the launch team and events we host</li>
    <li>Volunteer at community and networking outreach events</li>
  </ul>
  <p>Launch team members have no obligation to stay with the ministry once it's launched. Launch Team members are willing to use their time and talents to help establish another Kingdom Destination here in the earth. We'd love for you to stay around, but we rather you follow the purpose God has put in your heart.</p>
  <span class="btn red">JOIN OUR LAUNCH TEAM</span>
  <h4>Prayer Group</h4>
  <p>Pray for us as directed through email and video from Pastor Eli<br>Join our Prayer Team</p>
  <span class="btn navy">JOIN OUR PRAYER TEAM</span>
  <h4>Give</h4>
  <p>Pray for us as directed through email and video from Pastor Eli<br>Join our Prayer Team</p>
  <span class="btn red" style="width:194px">GIVE ONLINE</span>
</div>

<section class="values">
  <h2 class="heading" style="top:60px">CORE VALUES</h2>
</section>
<div class="vcard" style="left:506px;top:2342px"><div role="img" aria-label="Praying hands icon"></div></div>
<div class="vlabel" style="left:468px;top:2506px">Live with the Heart of God</div>
<div class="vcard" style="left:204px;top:2605px"><div role="img" aria-label="Figure with open arms icon"></div></div>
<div class="vlabel" style="left:166px;top:2770px">Love with the Heart of God</div>
<div class="vcard" style="left:810px;top:2605px"><div role="img" aria-label="Joined hands icon"></div></div>
<div class="vlabel" style="left:776px;top:2770px">Give with the Heart of God</div>
<div class="vcard" style="left:510px;top:2942px"><div role="img" aria-label="Hand offering a cross icon"></div></div>
<div class="vlabel" style="left:476px;top:3106px">Serve with the Heart of God</div>
<div class="ring"><div class="ring-inner"><i></i>RENEW</div></div>

<h2 class="heading" style="top:3246px">WHY OPEN ANOTHER CHURCH?</h2>
<ul class="why">
  <li>76% of people in the Milwaukee Metropolitan Area are not part of a faith community. There has to be an organization that addresses the needs of the people in this community.</li>
  <li>Milwaukee is known as one of the most segregated big cities in the United States. What better way to begin to break ground towards unity than by creating a worship space that reflects Heaven?</li>
  <li>Research shows only 10 percent of people who have a child with special needs are part of a faith community. We must address the physical and mental needs of families who have children with disabilities, showering them with the love of God and the support of a like-minded community</li>
  <li>Have you ever asked Why am I Here? What is my Purpose? If so, you are not alone. We help people find their purpose and connect them back to the community they serve.</li>
</ul>
<div class="video-back"></div>
<div class="video" role="img" aria-label="Worship crowd raising hands before a cross at sunset"></div>
<div class="video-frame"></div>
<svg class="abs" style="left:843px;top:3522px" width="56" height="56" viewBox="0 0 56 56"><circle cx="28" cy="28" r="27" fill="#fff"/><circle cx="28" cy="28" r="15" fill="#1b1b1b"/><polygon points="24,21 35,28 24,35" fill="#fff"/></svg>

<section class="community">
  <h2 class="heading" style="top:84px;color:#fff">COMMUNITY INVOLVEMENT</h2>
  <p>We are looking to partner with organizations that are making a difference in our community. If you are an organization which serves families with special needs, are focused on helping people develop in purpose, or helping to meet some of the basic needs of our community, we would love to explore collaboration and partnership to serve families.</p>
  <div class="group-photo" role="img" aria-label="Friends laughing together on a couch holding bibles"></div>
  <svg class="abs" style="left:214px;top:410px" width="40" height="64" viewBox="0 0 40 64"><polyline points="34,4 6,32 34,60" fill="none" stroke="#fff" stroke-width="5"/></svg>
  <svg class="abs" style="left:946px;top:410px" width="40" height="64" viewBox="0 0 40 64"><polyline points="6,4 34,32 6,60" fill="none" stroke="#fff" stroke-width="5"/></svg>
</section>

<div class="pastor-photo" role="img" aria-label="Pastor standing in a checked blazer"></div>
<h2 class="heading" style="top:4705px;left:351px;width:auto;text-align:left">PASTOR ELI</h2>
<ul class="pastor-list">
  <li>Pastor</li>
  <li>Teacher</li>
  <li>Husband</li>
  <li>Father of a Special Needs Child who is committed to your family's Spiritual Growth and Development</li>
</ul>

<footer class="footer">
  <div class="contact" style="left:112px;top:50px">
    <div class="ic"><svg width="22" height="16" viewBox="0 0 22 16"><rect x="1" y="1" width="20" height="14" fill="none" stroke="#d0151b" stroke-width="2"/><polyline points="1,1 11,9 21,1" fill="none" stroke="#d0151b" stroke-width="2"/></svg></div>
    <div><b>Email Address</b><span>info@renewlifechurch.org</span></div>
  </div>
  <div class="contact" style="left:392px;top:50px">
    <div class="ic"><svg width="20" height="20" viewBox="0 0 20 20"><path d="M4 1l4 4-2 3c1 3 3 5 6 6l3-2 4 4-3 3C8 19 1 12 1 4z" fill="#d0151b"/></svg></div>
    <div><b>Contact Number</b><span>414-555-0192</span></div>
  </div>
  <div class="contact" style="left:112px;top:130px">
    <div class="ic"><svg width="22" height="22" viewBox="0 0 22 22"><circle cx="11" cy="11" r="9" fill="none" stroke="#d0151b" stroke-width="2"/><ellipse cx="11" cy="11" rx="4" ry="9" fill="none" stroke="#d0151b" stroke-width="2"/><line x1="2" y1="11" x2="20" y2="11" stroke="#d0151b" stroke-width="2"/></svg></div>
    <div><b>Website</b><span>www.renewlifechurch.org</span></div>
  </div>
  <div class="contact" style="left:392px;top:130px">
    <div class="ic"><svg width="18" height="22" viewBox="0 0 18 22"><path d="M9 21C3 13 1 10 1 7a8 8 0 0116 0c0 3-2 6-8 14z" fill="#d0151b"/><circle cx="9" cy="7" r="3" fill="#fff"/></svg></div>
    <div><span>Renew Church,<br>Milwaukee Wisconsin.</span></div>
  </div>
  <div class="copy">© Copyright 2023 Renew Church | All Rights Reserved.</div>
  <div class="social"><i></i><i></i><i></i></div>
</footer>

<div class="form">
  <h3>REACH OUT US</h3>
  <div class="field">First Name</div>
  <div class="field">Last Name</div>
  <div class="field">Contact Number</div>
  <div class="field">Email Address</div>
  <div class="submit">SUBMIT NOW</div>
</div>

</body>
</html>
```